University Entrepreneurship Housing Cohort Needs a Flyer Design

Halvern Crest College's Venture and Discovery Center needs a flyer designed for their new "V-Nest" (short for Venture Nest) Living Learning Community.

The purpose of the V-Nest Living Learning Community (LLC) is to provide students at Halvern Crest College with the opportunity to live, learn, and participate in activities that have an entrepreneurship and innovation focus. Students with entrepreneurial ambitions will be able to connect with others who share those similar interests and aspirations. The community will create a space for students to learn about entrepreneurial and innovative ways of thinking and working, and to begin to implement their ideas using LLC provided resources (e.g,, workshops, site visits, mentors, and peer-networking). The LLC will also include an on-site V-Nest Lounge, which functions as a study space for V-Nest students. The lounge will have dry-erase walls, a 65-inch touch screen monitor, internet connectivity, and printing capabilities. The final design should communicate an exciting and innovative focused opportunity for young college students.

Note: Both logos need to be on the flyer, but pictures can be selected additionally as desired.

Target Market(s)

Undergraduate students who plan to live in on campus housing and have an interest in entrepreneurship and innovation

Industry/Entity Type

University

Font styles to use
Sans Serif

Requirements
Must have
• Both logos need to be on the flyer, but pictures can be selected additionally as desired.
• Font: Gill Sans (for larger text) and Usherwood (for smaller text)
• The purpose of the Venture Nest (V-Nest) Living Learning Community (LLC) is to provide students at Halvern Crest College with the opportunity to live, learn, and participate in activities that have an entrepreneurship and innovation focus.
• Students with entrepreneurial ambitions will be able to connect with others who share similar interests and aspirations. Using resources provided by the V-Nest LLC and the Venture and Discovery Center, residents will begin to develop their ideas, as well as participate in experiences that include workshops, competitions, mentorship, exposure to the Atlanta ecosystem, and peer-to-peer networking.
• The V-Nest Lounge will include:
• - Collaborative study space
• - Dry-erase walls
• - 65-inch touchscreen monitor
• - Internet connectivity
• - Printing capabilities
• Website: vdc.hcrest-demo.edu
• Phone: 555-270-3186
• Twitter: @HCCVDC
• Facebook: HCC_VDC
• LinkedIn: Venture & Discovery Center at Halvern Crest College
Nice to have
• Color codes:
• Blue PMS 286
• RED PMS 186
• Grey PMS 404
• More details here: http://brandbox.hcrest-demo.edu/guidelines/visual-identity/type-color-usage/

```html
<!DOCTYPE html>
<html lang="en">
<head>
<meta charset="utf-8">
<title>V-Nest Living Learning Community Flyer</title>
<link rel="stylesheet" href="https://fonts.googleapis.com/css2?family=Open+Sans:wght@300;400;700&family=Lustria&family=Roboto+Condensed:wght@400&display=swap">
<style>
  :root {
    --brand-blue: #1f3f99;
    --brand-blue-dark: #17307a;
    --brand-grey: #7a7b7e;
    --ring-grey: #c9cacc;
    --paper: #f2f2f2;
    --ink: #4a4b4d;
    --ink-soft: #58595b;
    --footer: #3c3c3e;
    --white: #ffffff;
  }
  html, body {
    margin: 0;
    padding: 0;
    width: 1016px;
    height: 1200px;
    overflow: hidden;
    background: var(--paper);
  }
  .flyer {
    position: relative;
    width: 1016px;
    height: 1200px;
    overflow: hidden;
    background: var(--paper);
    font-family: "Open Sans", sans-serif;
    color: var(--ink);
  }
  .flyer-shapes {
    position: absolute;
    inset: 0;
  }
  .masthead {
    position: absolute;
    left: 20px;
    top: 78px;
    width: 440px;
    text-align: center;
    color: var(--white);
  }
  .masthead-title {
    margin: 0;
    font-family: "Open Sans", sans-serif;
    font-weight: 400;
    font-size: 96px;
    line-height: 1;
    letter-spacing: -1px;
  }
  .masthead-subtitle {
    margin: 14px 0 0;
    font-family: "Lustria", serif;
    font-weight: 400;
    font-size: 38px;
    line-height: 1.12;
    letter-spacing: 1px;
  }
  .community-badge {
    position: absolute;
    left: 98px;
    top: 310px;
    width: 256px;
    height: 256px;
    display: flex;
    align-items: center;
    justify-content: center;
    font-family: "Open Sans", sans-serif;
    font-weight: 700;
    font-size: 52px;
    color: var(--brand-blue);
  }
  .college-lockup {
    position: absolute;
    left: 470px;
    top: 478px;
    width: 500px;
    text-align: center;
    font-family: "Open Sans", sans-serif;
    font-weight: 400;
    font-size: 27px;
    line-height: 1.3;
    color: var(--ink-soft);
  }
  .purpose {
    position: absolute;
    left: 78px;
    top: 594px;
    width: 895px;
    margin: 0;
    font-weight: 300;
    font-size: 21.5px;
    line-height: 1.4;
    color: var(--ink);
  }
  .lounge-banner {
    position: absolute;
    left: 44px;
    top: 707px;
    width: 449px;
    height: 58px;
    box-sizing: border-box;
    padding-left: 45px;
    background: var(--brand-blue);
    border-radius: 0 14px 14px 0;
    box-shadow: 3px 3px 0 var(--ring-grey);
    color: var(--white);
    font-weight: 700;
    font-size: 27px;
    line-height: 58px;
    letter-spacing: 0.5px;
    margin: 0;
  }
  .lounge-features {
    position: absolute;
    left: 97px;
    top: 774px;
    width: 900px;
    margin: 0;
    padding: 0;
    list-style: none;
    display: grid;
    grid-template-columns: 494px 1fr;
    row-gap: 4px;
    font-weight: 400;
    font-size: 25px;
    line-height: 36px;
    color: var(--ink);
    letter-spacing: 0.5px;
  }
  .feature {
    display: flex;
    align-items: center;
    gap: 10px;
  }
  .feature-icon {
    width: 22px;
    height: 22px;
    flex: none;
  }
  .gallery-photo {
    position: absolute;
    width: 200px;
    height: 200px;
    border-radius: 50%;
    box-sizing: border-box;
    border: 9px solid var(--ring-grey);
  }
  .gallery-photo--study {
    left: 253px; top: 885px;
    background: radial-gradient(circle at 40% 40%, #e9d8c7, #c98a7a 55%, #b23a3a);
  }
  .gallery-photo--atrium {
    left: 494px; top: 878px;
    width: 216px; height: 216px;
    background: linear-gradient(170deg, #cfe0ea 0%, #a7b7c3 35%, #8c5a42 70%, #5e4335 100%);
  }
  .gallery-photo--lounge {
    left: 763px; top: 885px;
    background: radial-gradient(circle at 50% 45%, #d9c2a8, #8a3f2e 55%, #4d2a22);
  }
  .contact-bar {
    position: absolute;
    left: 68px;
    top: 1125px;
    width: 948px;
    height: 75px;
    display: flex;
    align-items: center;
    color: var(--white);
  }
  .contact-cta {
    margin-left: 58px;
    font-family: "Roboto Condensed", sans-serif;
    font-size: 24px;
    letter-spacing: 0.3px;
  }
  .contact-item {
    display: flex;
    align-items: center;
    gap: 10px;
    font-family: "Open Sans", sans-serif;
    font-weight: 400;
    font-size: 27px;
  }
  .contact-item--phone { margin-left: 58px; }
  .contact-item--web { margin-left: 36px; }
  .contact-icon {
    width: 26px;
    height: 26px;
  }
</style>
</head>
<body>
<main class="flyer">

  <svg class="flyer-shapes" width="1016" height="1200" viewBox="0 0 1016 1200" aria-hidden="false">
    <defs>
      <linearGradient id="hero-tones" x1="0" y1="0" x2="1" y2="1">
        <stop offset="0" stop-color="#c9a27a"/>
        <stop offset="0.35" stop-color="#6b4a3a"/>
        <stop offset="0.65" stop-color="#c9b43a"/>
        <stop offset="1" stop-color="#d8d2cc"/>
      </linearGradient>
    </defs>

    <path class="hero-photo" role="img" aria-label="Photo: two students laughing together over a laptop in a dorm room"
          d="M380,0 H1016 V430 C880,370 700,372 530,430 L380,480 Z" fill="url(#hero-tones)"/>

    <path class="swoosh-grey"
          d="M0,480 C180,560 360,540 520,455 C700,370 880,368 1016,430 V470 C880,410 700,412 540,490 C380,570 190,600 0,540 Z"
          fill="var(--brand-grey)"/>

    <path class="masthead-panel-edge"
          d="M0,0 H548 C580,160 520,340 390,470 C300,548 120,540 0,500 Z"
          fill="var(--brand-grey)"/>
    <path class="masthead-panel"
          d="M0,0 H532 C562,160 505,330 380,458 C292,532 120,526 0,488 Z"
          fill="var(--brand-blue)"/>

    <path class="side-strip-edge"
          d="M0,548 C40,570 58,610 56,660 L58,1120 C62,1160 76,1186 96,1200 H0 Z"
          fill="var(--brand-grey)"/>
    <path class="side-strip"
          d="M0,556 C32,578 46,614 44,662 L46,1120 C50,1160 62,1186 80,1200 H0 Z"
          fill="var(--brand-blue)"/>

    <rect class="contact-bar-fill" x="68" y="1125" width="948" height="75" fill="var(--footer)"/>

    <circle class="badge-ring" cx="226" cy="438" r="130" fill="var(--ring-grey)"/>
    <circle class="badge-face" cx="226" cy="438" r="118" fill="var(--white)"/>
  </svg>

  <header class="masthead">
    <h1 class="masthead-title">V-Nest</h1>
    <p class="masthead-subtitle">Living Learning<br>Community</p>
  </header>

  <div class="community-badge">V-Nest</div>

  <div class="college-lockup">Halvern Crest College<br>Venture and Discovery Center</div>

  <p class="purpose">The purpose of the V-Nest Living Learning Community (LLC) is to provide under-graduate students at Halvern Crest College with the opportunity to live, learn, and participate in activities that have an entrepreneurship and innovation focus.</p>

  <h2 class="lounge-banner">THE LOUNGE WILL HAVE</h2>

  <ul class="lounge-features">
    <li class="feature"><svg class="feature-icon" viewBox="0 0 22 22"><circle cx="11" cy="11" r="10" fill="var(--ink-soft)"/><path d="M8.5,6.5 L15.5,11 L8.5,15.5 Z" fill="var(--paper)"/></svg>Dry-erase walls</li>
    <li class="feature"><svg class="feature-icon" viewBox="0 0 22 22"><circle cx="11" cy="11" r="10" fill="var(--ink-soft)"/><path d="M8.5,6.5 L15.5,11 L8.5,15.5 Z" fill="var(--paper)"/></svg>Internet connectivity</li>
    <li class="feature"><svg class="feature-icon" viewBox="0 0 22 22"><circle cx="11" cy="11" r="10" fill="var(--ink-soft)"/><path d="M8.5,6.5 L15.5,11 L8.5,15.5 Z" fill="var(--paper)"/></svg>65-inch touch screen monitor</li>
    <li class="feature"><svg class="feature-icon" viewBox="0 0 22 22"><circle cx="11" cy="11" r="10" fill="var(--ink-soft)"/><path d="M8.5,6.5 L15.5,11 L8.5,15.5 Z" fill="var(--paper)"/></svg>Printing capabilities</li>
  </ul>

  <div class="gallery-photo gallery-photo--study" role="img" aria-label="Photo: students talking during a study session in front of a whiteboard"></div>
  <div class="gallery-photo gallery-photo--atrium" role="img" aria-label="Photo: bright campus building atrium with a glass roof"></div>
  <div class="gallery-photo gallery-photo--lounge" role="img" aria-label="Photo: students working on laptops on a lounge sofa"></div>

  <footer class="contact-bar">
    <span class="contact-cta">CONTACT US TODAY</span>
    <span class="contact-item contact-item--phone">
      <svg class="contact-icon" viewBox="0 0 26 26"><circle cx="13" cy="13" r="11.5" fill="none" stroke="var(--white)" stroke-width="2"/><path d="M9,7.5 L11,7.5 L12,10.5 L10.8,11.6 C11.6,13.4 12.8,14.6 14.5,15.3 L15.6,14.1 L18.5,15.1 L18.5,17.2 C18.5,17.8 18,18.3 17.3,18.3 C12,18 8,14 7.8,8.7 C7.8,8 8.3,7.5 9,7.5 Z" fill="var(--white)"/></svg>
      555-270-3186
    </span>
    <span class="contact-item contact-item--web">
      <svg class="contact-icon" viewBox="0 0 26 26"><circle cx="13" cy="13" r="11.5" fill="none" stroke="var(--white)" stroke-width="2"/><ellipse cx="13" cy="13" rx="5" ry="11.5" fill="none" stroke="var(--white)" stroke-width="1.6"/><path d="M1.5,13 H24.5 M3.5,7 H22.5 M3.5,19 H22.5" stroke="var(--white)" stroke-width="1.6"/></svg>
      vdc.hcrest-demo.edu
    </span>
  </footer>

</main>
</body>
</html>
```